Corvane Capital Business Cards

These are professional business cards that are for my family office.
Put fake emails and phone numbers as of now until I finalize those components. This family office controls my families investments, assets, and future. The cards should be professional.
..
.
.
.
I just uploaded another variation of a logo I would like to see as a business card to I am inbeteen which logo to use

Target Market(s)

business

Industry/Entity Type

business

Contact Information for Business Card

Professional, wealth related, finance related.

Requirements
Must have
• Logo

```html
<!DOCTYPE html>
<html lang="en">
<head>
<meta charset="utf-8">
<title>Corvane Capital — Business Cards</title>
<link rel="stylesheet" href="https://fonts.googleapis.com/css2?family=Cinzel:wght@500&family=Montserrat:wght@400;600;700&display=swap">
<style>
  :root{
    --stage:#e9e7e3;
    --paper:#ffffff;
    --navy:#1b2130;
    --navy-ink:#161b28;
    --accent:#3f5196;
    --accent-soft:#4a5a9c;
    --muted:#9ea3ae;
    --text:#1e2230;
  }
  html,body{margin:0;padding:0;overflow:hidden;}
  body{width:900px;height:1200px;background:var(--stage);position:relative;font-family:"Montserrat",sans-serif;}
  .card{position:absolute;width:742px;height:440px;border-radius:24px;overflow:hidden;box-shadow:0 6px 18px rgba(0,0,0,.18);}
  .card--front{left:80px;top:131px;background:var(--paper);color:var(--text);}
  .card--back{left:79px;top:638px;background:var(--navy);color:#fff;}

  .wordmark{position:absolute;font-family:"Cinzel",serif;font-weight:500;white-space:nowrap;letter-spacing:.5px;line-height:1;}
  .card--front .wordmark{left:29px;top:50px;font-size:42px;color:var(--navy-ink);}
  .card--back .wordmark{left:32px;top:310px;font-size:36px;color:#fff;}

  .person{position:absolute;right:49px;top:60px;text-align:right;}
  .person__name{font-weight:700;font-size:27px;color:var(--navy-ink);line-height:1.1;}
  .person__role{font-size:15.5px;margin-top:2px;}

  .address{position:absolute;left:28px;top:250px;font-size:16.5px;line-height:20px;}
  .contacts{position:absolute;left:28px;top:323px;list-style:none;margin:0;padding:0;font-size:16.5px;}
  .contacts li{display:flex;align-items:center;height:28px;}
  .contacts svg{width:16px;height:16px;margin-right:10px;fill:var(--navy-ink);}

  .emblem{position:absolute;}
  .card--front .emblem{left:466px;top:170px;width:248px;height:248px;}
  .card--back .emblem{left:376px;top:8px;width:420px;height:420px;}
  .emblem__name{font-family:"Cinzel",serif;font-weight:500;}
  .card--front .emblem__name{font-size:30px;fill:var(--navy-ink);}
  .card--back .emblem__name{font-size:50px;fill:var(--accent-soft);opacity:.55;}

  .back-url{position:absolute;left:58px;top:355px;font-weight:700;font-size:18.5px;color:var(--muted);letter-spacing:.3px;}
</style>
</head>
<body>
  <section class="card card--front" aria-label="Business card front">
    <div class="wordmark">Corvane Capital</div>
    <div class="person">
      <div class="person__name">Martin Alvarez</div>
      <div class="person__role">Owner</div>
    </div>
    <svg class="emblem" viewBox="0 0 248 248" role="img" aria-label="Corvane Capital mark">
      <circle cx="124" cy="124" r="120" fill="none" stroke="var(--navy-ink)" stroke-width="4"/>
      <text class="emblem__name" x="124" y="118" text-anchor="middle">Corvane</text>
      <text class="emblem__name" x="124" y="154" text-anchor="middle">Capital</text>
    </svg>
    <div class="address">48 Linden Court Plaza<br>Harwell, NJ 07841 USA</div>
    <ul class="contacts">
      <li><svg viewBox="0 0 16 16"><path d="M3.5 1.5l2.3 2.6-1.2 1.8c.8 1.8 2.6 3.6 4.4 4.5l1.8-1.2 2.6 2.3-1.4 2.2C7 13.5 2.5 9 1.4 2.9z"/></svg>(555)214-7730</li>
      <li><svg viewBox="0 0 16 16"><path d="M1 3.5h14v1.2L8 9 1 4.7zM1 6.3l7 4.3 7-4.3v6.2H1z"/></svg>info@yourwebsitename.com</li>
      <li><svg viewBox="0 0 16 16"><path d="M8 1a7 7 0 100 14A7 7 0 008 1zm-1 2.2c-.4 1-1.8 1.2-2 2.3.6.9 1.9.4 2.5 1.3.3.9-.7 1.6-.2 2.6.5.8.3 2.2.8 2.8C5.3 12 3 10.2 3 8c0-2.2 1.7-4.1 4-4.8zm3 .4c1.8.6 3 2.3 3 4.3 0 1-.3 1.9-.8 2.6-.5-.8-1.5-.9-1.9-1.9-.3-.8.6-1.5.2-2.3-.4-.9-1.5-.5-1.8-1.3-.2-.5.8-1 1.3-1.4z"/></svg>www.yourwebsitename.com</li>
    </ul>
  </section>

  <section class="card card--back" aria-label="Business card back">
    <svg class="emblem" viewBox="0 0 420 420" role="img" aria-label="Corvane Capital mark, large decoration">
      <circle cx="210" cy="210" r="200" fill="none" stroke="var(--accent)" stroke-width="6" opacity=".75"/>
      <text class="emblem__name" x="190" y="200" text-anchor="middle">Corvane</text>
      <text class="emblem__name" x="190" y="258" text-anchor="middle">Capital</text>
    </svg>
    <div class="wordmark">Corvane Capital</div>
    <div class="back-url">www.yourwebsitename.com</div>
  </section>
</body>
</html>
```